Schriftdesign für Shop-Header Bild (Schmuckhandel) / Online-Marketing Material
Wir verkaufen Schmuck im Onlineshop mit Herz
Wir benötigen den vorgegebenen Text in schöner Form, Farbe und Größe harmonisch eingefügt, in unserem Bild.
Folgender Text soll sich schick ins Bild einfügen oder in 3-D vielleicht in Schriftfarbe gold hervorheben:
Mit ganzem Herzen für Sie da!
Ihr Online -Juwelier mit Herz
Siehe auch unser altes Bild mit Text, im Shop, wie es nicht aussehen sollte: www.sonnenflocke.de

```html
<!DOCTYPE html>
<html lang="de">
<head>
<meta charset="utf-8">
<title>Mit ganzem Herzen – Shop-Header</title>
<link rel="stylesheet" href="https://fonts.googleapis.com/css2?family=Allura&family=Fira+Sans+Extra+Condensed:wght@200;300&family=Lato:wght@400&display=swap">
<style>
  :root {
    --page-bg: #ffffff;
    --band-tan: #a89478;
    --silk-light: #d9c6c4;
    --silk-mid: #9d7b80;
    --silk-deep: #6e4d55;
    --shadow-dark: #24090f;
    --gold-soft: #dcc4ab;
    --white: #ffffff;
  }
  html, body {
    margin: 0;
    width: 1200px;
    height: 1200px;
    overflow: hidden;
    background: var(--page-bg);
  }
  .canvas {
    position: relative;
    width: 1200px;
    height: 1200px;
  }
  .header-banner {
    position: absolute;
    left: 40px;
    top: 506px;
    width: 1120px;
    height: 187px;
    overflow: hidden;
  }
  .header-banner__band {
    position: absolute;
    left: 0; top: 0;
    width: 100%;
    height: 15px;
    background: var(--band-tan);
  }
  .header-banner__photo {
    position: absolute;
    left: 0; top: 15px;
    width: 1120px;
    height: 172px;
    display: block;
  }
  .headline {
    position: absolute;
    margin: 0;
    line-height: 1;
    white-space: nowrap;
  }
  .headline__lead {
    left: 790px;
    top: 24px;
    font-family: "Fira Sans Extra Condensed", sans-serif;
    font-weight: 200;
    font-size: 31px;
    color: var(--gold-soft);
  }
  .headline__script {
    left: 680px;
    top: 34px;
    font-family: "Allura", cursive;
    font-size: 84px;
    color: var(--white);
  }
  .headline__close {
    left: 714px;
    top: 111px;
    font-family: "Fira Sans Extra Condensed", sans-serif;
    font-weight: 200;
    font-size: 40px;
    color: var(--gold-soft);
  }
  .tagline {
    position: absolute;
    left: 0;
    width: 1352px;
    top: 160px;
    margin: 0;
    text-align: center;
    font-family: "Lato", sans-serif;
    font-size: 11px;
    letter-spacing: 8px;
    color: var(--white);
    line-height: 1;
  }
</style>
</head>
<body>
<main class="canvas">
  <section class="header-banner">
    <div class="header-banner__band"></div>
    <svg class="header-banner__photo" viewBox="0 0 1120 172" role="img" aria-label="Foto: goldener Herzanhänger an feiner Goldkette auf altrosa Seidenstoff">
      <defs>
        <linearGradient id="silkHorizontal" x1="0" y1="0" x2="1" y2="0">
          <stop offset="0" stop-color="#c9b0ae"/>
          <stop offset="0.2" stop-color="var(--silk-light)"/>
          <stop offset="0.45" stop-color="#b89a98"/>
          <stop offset="0.75" stop-color="var(--silk-mid)"/>
          <stop offset="1" stop-color="var(--silk-deep)"/>
        </linearGradient>
        <linearGradient id="silkShade" x1="0" y1="0" x2="0" y2="1">
          <stop offset="0" stop-color="var(--shadow-dark)" stop-opacity="0"/>
          <stop offset="0.55" stop-color="var(--shadow-dark)" stop-opacity="0.1"/>
          <stop offset="0.82" stop-color="var(--shadow-dark)" stop-opacity="0.85"/>
          <stop offset="1" stop-color="var(--shadow-dark)" stop-opacity="1"/>
        </linearGradient>
        <radialGradient id="pendantGlow" cx="0.5" cy="0.5" r="0.5">
          <stop offset="0" stop-color="#d8b374" stop-opacity="0.55"/>
          <stop offset="1" stop-color="#d8b374" stop-opacity="0"/>
        </radialGradient>
      </defs>
      <rect width="1120" height="172" fill="url(#silkHorizontal)"/>
      <ellipse cx="560" cy="80" rx="90" ry="70" fill="url(#pendantGlow)"/>
      <rect width="1120" height="172" fill="url(#silkShade)"/>
    </svg>
    <p class="headline headline__lead">MIT GANZEM</p>
    <p class="headline headline__script">Herzen</p>
    <p class="headline headline__close">für Sie da!</p>
    <p class="tagline">IHR ONLINE-JUWELIER MIT HERZ</p>
  </section>
</main>
</body>
</html>
```